Business Card - connecting 2 souls and beggining the journey of self discovery

Logo on the front
with tag line

On the back list of services and contact details

Seminars
workshops
Coaching
podcasts

Darren Whitlow
Health & Wellbeing Life Coach
0491 372 615
darren@brightcoreliving.example
brightcoreliving.example

Industry/Entity Type

Life Coaching

Contact Information for Business Card

I like the use of colour from the logo to be used. I'm not a fan of white.

Requirements
Must have
• My tagline: The journey home starts with you
Nice to have
• Use of colour that is in the Brightcore Living logo

```html
<!DOCTYPE html>
<html lang="en">
<head>
<meta charset="utf-8">
<title>Brightcore Living – Business Card</title>
<link rel="stylesheet" href="https://fonts.googleapis.com/css2?family=Open+Sans:wght@400;600;700&display=swap">
<style>
  :root {
    --backdrop: #3a322d;
    --card: #141414;
    --card-edge: #1d1d1d;
    --silver: #8d8d8d;
    --silver-soft: #6e6e6e;
    --text-light: #f1f1f1;
    --accent-green: #3fbf8a;
    --accent-pink: #f0506e;
    --divider: #5a5a5a;
  }
  * { box-sizing: border-box; margin: 0; padding: 0; }
  html, body {
    width: 1200px;
    height: 864px;
    overflow: hidden;
    background: var(--backdrop);
    font-family: "Open Sans", sans-serif;
  }
  .canvas {
    position: relative;
    width: 1200px;
    height: 864px;
  }
  .card {
    position: absolute;
    width: 540px;
    height: 310px;
    background: var(--card);
    border: 1px solid var(--card-edge);
    box-shadow: 0 14px 30px rgba(0,0,0,0.45);
  }
  /* Front card */
  .card--front {
    left: 50px;
    top: 120px;
  }
  .front-brand {
    position: absolute;
    top: 46px;
    left: 0;
    right: 0;
    display: flex;
    align-items: center;
    justify-content: center;
    gap: 12px;
  }
  .front-brand__dot {
    width: 26px;
    height: 26px;
    border-radius: 50%;
    background: var(--silver-soft);
  }
  .front-brand__name {
    font-size: 20px;
    font-weight: 600;
    color: var(--silver);
    letter-spacing: 0.5px;
  }
  .front-tagline {
    position: absolute;
    top: 132px;
    left: 20px;
    right: 20px;
    text-align: center;
    font-size: 27px;
    font-weight: 400;
    color: var(--silver);
    letter-spacing: -0.5px;
    white-space: nowrap;
  }
  .front-services {
    position: absolute;
    top: 196px;
    left: 0;
    right: 0;
    display: flex;
    justify-content: center;
    align-items: center;
    gap: 10px;
    font-size: 16px;
    color: var(--silver);
  }
  .front-services .sep {
    width: 5px;
    height: 5px;
    border-radius: 50%;
    background: var(--accent-green);
  }
  /* Back card */
  .card--back {
    left: 610px;
    top: 434px;
  }
  .back-brand {
    position: absolute;
    left: 30px;
    top: 0;
    bottom: 0;
    width: 170px;
    display: flex;
    flex-direction: column;
    align-items: center;
    justify-content: center;
    gap: 12px;
  }
  .back-brand__dot {
    width: 70px;
    height: 70px;
    border-radius: 50%;
    background: var(--accent-green);
  }
  .back-brand__name {
    font-size: 17px;
    font-weight: 600;
    color: var(--text-light);
    text-align: center;
  }
  .back-divider {
    position: absolute;
    left: 218px;
    top: 80px;
    width: 1px;
    height: 150px;
    background: var(--divider);
  }
  .contact {
    position: absolute;
    left: 240px;
    top: 88px;
  }
  .contact__name {
    font-size: 19px;
    font-weight: 700;
    color: var(--accent-green);
    text-transform: uppercase;
    line-height: 1.15;
  }
  .contact__role {
    font-size: 16px;
    font-weight: 700;
    color: var(--accent-pink);
    text-transform: uppercase;
    line-height: 1.3;
    margin-bottom: 10px;
  }
  .contact__list { list-style: none; }
  .contact__item {
    display: flex;
    align-items: center;
    gap: 9px;
    font-size: 15px;
    color: var(--text-light);
    line-height: 1.45;
  }
  .contact__icon {
    width: 13px;
    height: 13px;
    flex: none;
  }
</style>
</head>
<body>
<main class="canvas">

  <section class="card card--front" aria-label="Card front">
    <div class="front-brand">
      <span class="front-brand__dot"></span>
      <span class="front-brand__name">Brightcore Living</span>
    </div>
    <p class="front-tagline">The journey home starts with you</p>
    <p class="front-services">
      <span>Seminars</span><span class="sep"></span>
      <span>Workshops</span><span class="sep"></span>
      <span>Coaching</span><span class="sep"></span>
      <span>Podcasts</span>
    </p>
  </section>

  <section class="card card--back" aria-label="Card back">
    <div class="back-brand">
      <span class="back-brand__dot"></span>
      <span class="back-brand__name">Brightcore Living</span>
    </div>
    <div class="back-divider"></div>
    <div class="contact">
      <p class="contact__name">Darren Whitlow</p>
      <p class="contact__role">Health &amp; Wellbeing Life Coach</p>
      <ul class="contact__list">
        <li class="contact__item">
          <svg class="contact__icon" viewBox="0 0 16 16" aria-hidden="true">
            <path fill="#3fbf8a" d="M3.6 1.5l2.3 2.6-1.3 1.8c.9 2 2.5 3.6 4.5 4.5l1.8-1.3 2.6 2.3-1.2 2.1C7.4 13.3 2.7 8.6 1.5 3.7z"/>
          </svg>
          <span>0491 372 615</span>
        </li>
        <li class="contact__item">
          <svg class="contact__icon" viewBox="0 0 16 16" aria-hidden="true">
            <rect x="1" y="3" width="14" height="10" rx="1.5" fill="#3fbf8a"/>
            <path d="M1.5 4l6.5 5 6.5-5" fill="none" stroke="#141414" stroke-width="1.4"/>
          </svg>
          <span>darren@brightcoreliving.example</span>
        </li>
        <li class="contact__item">
          <svg class="contact__icon" viewBox="0 0 16 16" aria-hidden="true">
            <circle cx="8" cy="8" r="7" fill="#3fbf8a"/>
            <path d="M1 8h14M8 1c-2.5 2.5-2.5 11.5 0 14M8 1c2.5 2.5 2.5 11.5 0 14" fill="none" stroke="#141414" stroke-width="1"/>
          </svg>
          <span>www.brightcoreliving.example</span>
        </li>
      </ul>
    </div>
  </section>

</main>
</body>
</html>
```